For Lease Sign to Attract National Retail Tenants

Attached is a logo design that was created by Pixel Harbor. I will like to develop a leasing sign that is 4 foot wide by 4 foot high or 4 feet wide and 6 feet high. I would like the sign to have a black background and use the colors that are in the logo. These will be signs that are placed in front of shopping centers and are often read by passing motorist so the sign must be simple, clean, very easy to read, distinctive, and have as few words as possible. It would be good if small amounts of bright green can be added as a boarder or ????? The text should be FOR LEASE, 415-738-2916, Rod Kellaway. I will want to also design cards and letter head around the same theme.

Target Market(s)

National retail tenants wanting to lease space in my shopping centers

Industry/Entity Type

Real Estate Development

Contact Information for Business Card

Tall Oak Holdings, LLC Rod Kellaway President & CEO 4127 Marlow Ave. Suite 308 La Jolla, CA 92037 415-738-2916 rodkellaway@quillpost.net

```html
<!DOCTYPE html>
<html lang="en">
<head>
<meta charset="utf-8">
<title>For Lease Sign – Tall Oak Holdings</title>
<link href="https://fonts.googleapis.com/css2?family=Montserrat:wght@500;900&display=swap" rel="stylesheet">
<style>
  :root {
    --canvas-grey: #d9dad9;
    --sign-black: #0d0d0d;
    --brand-red: #e41e2b;
    --brand-grey: #c9c9c9;
    --red-light: #f2604f;
    --red-mid: #e8392c;
    --red-deep: #b8141e;
    --border-green: #39e43c;
    --headline-white: #ffffff;
  }
  html, body {
    margin: 0;
    padding: 0;
    width: 1200px;
    height: 1200px;
    overflow: hidden;
    background: var(--canvas-grey);
  }
  .lease-sign {
    position: absolute;
    left: 361px;
    top: 250px;
    width: 490px;
    height: 743px;
    display: block;
  }
  .sign-face { fill: var(--sign-black); }
  .accent-line { fill: none; stroke: var(--brand-red); }
  .accent-line--grey { stroke: var(--brand-grey); }
  .gap-line { fill: none; stroke: var(--sign-black); }
  .green-border { fill: none; stroke: var(--border-green); }
  .brand-name {
    font-family: "Montserrat", sans-serif;
    font-weight: 500;
    font-size: 27px;
    letter-spacing: 1px;
    fill: var(--brand-red);
  }
  .phone {
    font-family: "Montserrat", sans-serif;
    font-weight: 500;
    font-size: 58px;
    fill: var(--brand-red);
  }
  .contact-name {
    font-family: "Montserrat", sans-serif;
    font-weight: 500;
    font-size: 42px;
    fill: var(--brand-grey);
  }
  .headline {
    font-family: "Montserrat", sans-serif;
    font-weight: 900;
    font-size: 134px;
    fill: var(--headline-white);
  }
</style>
</head>
<body>
<svg class="lease-sign" viewBox="0 0 612 929" xmlns="http://www.w3.org/2000/svg" aria-label="For Lease sign">
  <defs>
    <radialGradient id="redGlow" cx="130" cy="520" r="560" gradientUnits="userSpaceOnUse">
      <stop offset="0" stop-color="var(--red-light)"/>
      <stop offset="0.55" stop-color="var(--red-mid)"/>
      <stop offset="1" stop-color="var(--red-deep)"/>
    </radialGradient>
  </defs>

  <rect class="sign-face" x="0" y="0" width="612" height="929"/>

  <path class="red-wave" fill="url(#redGlow)"
        d="M0,0 L36,0 C48,140 110,250 190,322 L360,470 C470,570 585,690 612,793 L612,929 L0,929 Z"/>

  <path class="accent-line accent-line--grey" stroke-width="5" d="M62,0 C68,85 92,160 130,212"/>
  <path class="gap-line" stroke-width="11" d="M392,478 C500,585 565,700 572,929"/>
  <path class="accent-line accent-line--grey" stroke-width="6" d="M402,482 C512,592 578,705 586,929"/>

  <text class="brand-name" x="385" y="164" text-anchor="middle">TALL OAK HOLDINGS</text>
  <text class="phone" x="385" y="266" text-anchor="middle">415-738-2916</text>
  <text class="contact-name" x="385" y="319" text-anchor="middle">Rod Kellaway</text>

  <text class="headline" x="259" y="664" text-anchor="middle">FOR</text>
  <text class="headline" x="272" y="795" text-anchor="middle">LEASE</text>

  <rect class="green-border" x="6" y="6" width="600" height="917" stroke-width="12"/>
</svg>
</body>
</html>
```